business card deign

Logo needs the following on it.
1. attached logo
2. Tagline - "If it keeps a drink cold or the party going...we do it!"
3. Name- Dalton Pikes, Founder and CPO
4. Address - 412 E. Carver Avenue, Ste 2207, Tampa, FL. 33917
5. Phone - 555.318.4726

```html
<!DOCTYPE html>
<html lang="en">
<head>
<meta charset="utf-8">
<title>Kelvaro Business Card</title>
<link href="https://fonts.googleapis.com/css2?family=Montserrat:wght@400;500;700&display=swap" rel="stylesheet">
<style>
  :root {
    --backdrop: #9b9b9b;
    --card-light: #ffffff;
    --card-dark: #000000;
    --ink: #111111;
    --ink-soft: #1c1c1c;
    --paper-text: #f2f2f2;
  }
  * { box-sizing: border-box; margin: 0; padding: 0; }
  html, body {
    width: 1093px;
    height: 1200px;
    overflow: hidden;
    background: var(--backdrop);
    font-family: "Montserrat", sans-serif;
  }
  .card {
    position: absolute;
    left: 264px;
    width: 581px;
    height: 364px;
    border-radius: 20px;
    box-shadow: 2px 3px 5px rgba(0,0,0,0.45);
  }
  .card--front { top: 225px; background: var(--card-light); color: var(--ink); }
  .card--back { top: 616px; background: var(--card-dark); color: var(--paper-text); }

  .person { position: absolute; left: 29px; top: 55px; }
  .person__name { font-size: 22px; font-weight: 700; line-height: 1.1; letter-spacing: -0.2px; }
  .person__role { font-size: 13px; font-weight: 400; margin-top: 2px; }

  .wordmark {
    position: absolute;
    font-weight: 700;
    text-align: center;
    white-space: nowrap;
  }
  .card--front .wordmark {
    right: 30px;
    top: 110px;
    font-size: 23px;
    letter-spacing: 9px;
    color: var(--ink);
  }
  .card--back .wordmark {
    left: 0; right: 0;
    top: 218px;
    font-size: 40px;
    letter-spacing: 20px;
    padding-left: 20px;
    color: var(--paper-text);
  }

  .contact { position: absolute; left: 29px; top: 262px; list-style: none; }
  .contact__item {
    display: flex; align-items: center;
    font-size: 13px; height: 26px;
    color: var(--ink-soft);
  }
  .contact__icon { width: 14px; height: 14px; margin-right: 8px; fill: var(--ink); }

  .address {
    position: absolute; left: 365px; top: 297px;
    font-size: 13px; line-height: 16px; font-style: normal;
    color: var(--ink-soft);
  }

  .tagline {
    position: absolute; left: 0; right: 0; top: 317px;
    text-align: center; font-size: 13.5px; font-weight: 400;
  }
</style>
</head>
<body>
  <section class="card card--front">
    <div class="person">
      <h1 class="person__name">Dalton Pikes</h1>
      <p class="person__role">Founder and CPO</p>
    </div>
    <div class="wordmark">KELVARO</div>
    <ul class="contact">
      <li class="contact__item">
        <svg class="contact__icon" viewBox="0 0 24 24"><path d="M6.6 10.8a15.1 15.1 0 0 0 6.6 6.6l2.2-2.2a1 1 0 0 1 1-.25 11.4 11.4 0 0 0 3.6.6 1 1 0 0 1 1 1V20a1 1 0 0 1-1 1A17 17 0 0 1 3 4a1 1 0 0 1 1-1h3.5a1 1 0 0 1 1 1c0 1.25.2 2.45.6 3.6a1 1 0 0 1-.25 1z"/></svg>
        555.318.4726
      </li>
      <li class="contact__item">
        <svg class="contact__icon" viewBox="0 0 24 24"><path d="M2 5h20v2l-10 6L2 7z"/><path d="M2 9l10 6 10-6v10H2z"/></svg>
        info@kelvaro.com
      </li>
      <li class="contact__item">
        <svg class="contact__icon" viewBox="0 0 24 24"><circle cx="12" cy="12" r="10"/><path d="M7 7c2 0 3 1 3 3s-2 2-2 4 2 2 2 4M15 5c-1 2 1 3 2 3s2 2 1 4-2 1-3 3 1 3 1 4" stroke="#fff" stroke-width="1.6" fill="none"/></svg>
        www.kelvaro.com
      </li>
    </ul>
    <address class="address">412 E. Carver Avenue, Ste 2207,<br>Tampa, FL. 33917</address>
  </section>

  <section class="card card--back">
    <div class="wordmark">KELVARO</div>
    <p class="tagline">If it keeps a drink cold or the party going...we do it</p>
  </section>
</body>
</html>
```